Family business needs stationery redesign with new logo

Family owned company, established in 1987 wanting a brand 'refresh'. We are an electrical, refrigeration and construction company based in the Barkly Region Northern Territory, Australia. We have a new logo we would like to use which is uploaded along with our current letterhead and email signature. We are also dropping the word 'contractors' so please do not include this on any designs. Please note also, the 'orange' color used in our logo and designs should be Northern Territory red ochre which is as follows:

RGB (Hex): #C75B12
PantoneĀ® 159 C
CMYK: 1 / 74 / 100 / 7

We are needing our stationery redesigned using our new logo. Please include letterheads, business cards, envelopes, and email signatures.

We currently use our business letterheads for quotations, invoices, letters, HR matters, and internal memos.

We also need a separate simplified letterhead for internal paperwork such as employee leave forms, meeting agendas, and meeting minutes etc.

Reason: Needing more submissions of full package designs. We are wanting all our stationery, including business cards, letterheads, email signatures, envelopes, etc to be cohesive. We also require ALL the information, as supplied on our template letterhead, to be included on the new letterhead designs. including electrical license no.etc Thank you, R&W

Reason: needing more time as work has got in the way of looking over designs. A lot of designs not meeting the brief/criteria.

Industry/Entity Type

Business

Colors
0355a3
f37122

Requirements
Must have
• The 'orange' color used in the designs should be Northern Territory red ochre which is as follows:
• RGB (Hex): #C75B12
• PantoneĀ® 159 C
• CMYK: 1 / 74 / 100 / 7
• ***MUST INCLUDE ALL INFORMATION THAT IS ON OUR CURRENT LETTERHEAD***
Should not have
• Please do not include the word 'contractors'

```html
<!DOCTYPE html>
<html lang="en">
<head>
<meta charset="utf-8">
<title>R&amp;W Business Card</title>
<link rel="stylesheet" href="https://fonts.googleapis.com/css2?family=Source+Sans+3:wght@400;600;700&display=swap">
<style>
  :root {
    --navy: #1b3070;
    --ochre: #c75b12;
    --white: #ffffff;
    --page: #e4e4e4;
  }
  * { box-sizing: border-box; margin: 0; padding: 0; }
  html, body {
    width: 1200px; height: 987px; overflow: hidden;
    background: var(--page);
    font-family: "Source Sans 3", "Myriad Pro", Arial, sans-serif;
  }
  .card {
    position: absolute; left: 293px; width: 616px; height: 352px;
    border-radius: 19px; overflow: hidden;
  }
  .card--front { top: 130px; background: var(--white); }
  .card--back { top: 505px; background: var(--ochre); }

  .wordmark {
    position: absolute; left: 0; right: 0; text-align: center;
    font-weight: 700; letter-spacing: 2px; line-height: 1;
  }
  .card--front .wordmark { top: 64px; font-size: 88px; color: var(--navy); }
  .card--back .wordmark { top: 131px; font-size: 88px; color: var(--white); }

  .info-band {
    position: absolute; left: 0; right: 0; top: 205px; bottom: 0;
    background: var(--navy);
  }
  .info-band::before {
    content: ""; position: absolute; left: 0; right: 0; top: 4px; height: 3px;
    background: var(--ochre);
  }
  .identity { position: absolute; left: 35px; top: 31px; color: var(--white); }
  .identity__name {
    color: var(--ochre); font-size: 22px; font-weight: 600; line-height: 26px;
  }
  .identity__title { font-size: 17px; line-height: 22px; margin-bottom: 3px; }
  .identity__address { font-size: 16px; line-height: 22px; }

  .contacts {
    position: absolute; right: 35px; top: 33px; list-style: none;
    color: var(--white); font-size: 16px; line-height: 23.5px; text-align: right;
  }
  .contacts li { display: flex; justify-content: flex-end; align-items: center; gap: 8px; }
  .contacts svg { width: 15px; height: 15px; fill: var(--ochre); flex: none; }

  .card__web {
    position: absolute; left: 0; right: 0; top: 294px; text-align: center;
    color: var(--white); font-size: 15px; letter-spacing: 2px;
  }
</style>
</head>
<body>
  <section class="card card--front">
    <div class="wordmark">R&amp;W</div>
    <div class="info-band">
      <div class="identity">
        <p class="identity__name">ERIN MADDOX</p>
        <p class="identity__title">CEO/FOUNDER</p>
        <p class="identity__address">4120 Wattle Creek Road</p>
        <p class="identity__address">Tennant Creek, NT 0860</p>
      </div>
      <ul class="contacts">
        <li>614 552 0837
          <svg viewBox="0 0 16 16" aria-hidden="true"><path d="M3.5 1l2.5 3-1.5 2c.8 2 2.6 3.8 4.5 4.5l2-1.5 3 2.5-1.5 2.5C7 14 2 9 1 2.5z"/></svg>
        </li>
        <li>614 552 0912
          <svg viewBox="0 0 16 16" aria-hidden="true"><path d="M4 1h8v4H4zM1 6h14v6h-3v3H4v-3H1zM5 10v3h6v-3z"/></svg>
        </li>
        <li>office@rwgroup.net
          <svg viewBox="0 0 16 16" aria-hidden="true"><path d="M1 3h14v1.5L8 9 1 4.5zM1 6.3l7 4.5 7-4.5V13H1z"/></svg>
        </li>
        <li>www.rwgroup.net
          <svg viewBox="0 0 16 16" aria-hidden="true"><path d="M8 1a7 7 0 1 0 0 14A7 7 0 0 0 8 1zm-1 2.2c-.8 1-1.6 1.8-1 3 .7 1.2 2.3.6 2.6 2 .2 1.1-1.3 1.5-1 3 .1.6.6 1 .9 1.7A5.6 5.6 0 0 1 2.5 7.5c1 .2 1.5-.6 2-1.6C5 4.6 5.9 3.6 7 3.2zm3.4.5a5.6 5.6 0 0 1 2.9 6.6c-.7-.7-1.6-.5-2-1.6-.3-1 .6-1.6.1-2.6-.4-.9-1.6-.7-1.6-1.6 0-.4.3-.7.6-.8z"/></svg>
        </li>
      </ul>
    </div>
  </section>

  <section class="card card--back">
    <div class="wordmark">R&amp;W</div>
    <p class="card__web">www.rwgroup.net</p>
  </section>
</body>
</html>
```